Card Design for my dog training business Brightpaw Obedience

Need a business card design for my dog training business with my new logo. Want the card to come off professional yet fun. Want it to be very eye catchy as well. I normally have these at vet clinics, pet stores, and groomers. so need it to look better than my competitors.
Target Market(s)
dog owners
Industry/Entity Type
Dog Training
Contact Information for Business Card
needs logo, my name and info
Font styles to use
Serif
Colors
0255a3
ffffff
ec1f27
000000
333333
fbfbfb
Requirements
Must have
- Brightpaw Obedience
- Felix Orland
- 415 903 2276
- info@brightpawobedience.example
- www.brightpawobedience.example

```html
<!DOCTYPE html>
<html lang="en">
<head>
<meta charset="utf-8">
<title>Brightpaw Obedience – Business Card</title>
<link rel="stylesheet" href="https://fonts.googleapis.com/css2?family=EB+Garamond:ital@0;1&family=Lato:wght@400&family=Tinos&display=swap">
<style>
  :root {
    --brand-blue: #0255a3;
    --white: #ffffff;
    --page: #f1f1f1;
    --shadow: rgba(0, 0, 0, 0.35);
  }
  html, body {
    margin: 0;
    width: 1200px;
    height: 900px;
    overflow: hidden;
    background: var(--page);
  }
  .canvas {
    position: relative;
    width: 1200px;
    height: 900px;
  }
  .card {
    position: absolute;
    box-shadow: 2px 3px 5px var(--shadow);
    box-sizing: border-box;
  }
  .card--front {
    left: 330px;
    top: 90px;
    width: 555px;
    height: 343px;
    background: var(--brand-blue);
    color: var(--white);
    text-align: center;
  }
  .holder-name {
    position: absolute;
    top: 82px;
    left: 0;
    right: 0;
    margin: 0;
    font-family: "Tinos", "Times New Roman", serif;
    font-weight: 400;
    font-size: 24px;
    letter-spacing: 0.5px;
  }
  .icon-row {
    position: absolute;
    top: 152px;
    left: 0;
    right: 0;
    display: flex;
    justify-content: center;
    align-items: center;
    gap: 5px;
  }
  .icon-row .rule {
    width: 58px;
    height: 2px;
    background: var(--white);
    margin: 0 4px;
  }
  .icon-row svg {
    display: block;
    width: 24px;
    height: 24px;
  }
  .contact-list {
    position: absolute;
    top: 184px;
    left: 0;
    right: 0;
    margin: 0;
    padding: 0;
    list-style: none;
    font-family: "Lato", Arial, sans-serif;
    font-size: 18.5px;
    line-height: 24.5px;
  }
  .card--back {
    left: 330px;
    top: 469px;
    width: 559px;
    height: 343px;
    background: var(--white);
  }
  .brand-name {
    position: absolute;
    top: 148px;
    left: 0;
    right: 0;
    margin: 0;
    text-align: center;
    font-family: "EB Garamond", Georgia, serif;
    font-weight: 400;
    font-size: 36px;
    color: var(--brand-blue);
    letter-spacing: 0.5px;
  }
  .tagline-band {
    position: absolute;
    left: 0;
    right: 0;
    bottom: 0;
    height: 46px;
    background: var(--brand-blue);
    display: flex;
    align-items: center;
    justify-content: center;
  }
  .tagline {
    margin: 0;
    font-family: "EB Garamond", Georgia, serif;
    font-style: italic;
    font-size: 17px;
    color: var(--white);
  }
</style>
</head>
<body>
<main class="canvas">
  <section class="card card--front" aria-label="Card front">
    <h1 class="holder-name">FELIX ORLAND</h1>
    <div class="icon-row">
      <span class="rule"></span>
      <svg viewBox="0 0 24 24" aria-label="Phone">
        <rect width="24" height="24" fill="#ffffff"/>
        <path d="M5 10c0-3 3-4 7-4s7 1 7 4l-3 0 0-2-8 0 0 2z" fill="#0255a3"/>
        <rect x="7" y="11" width="10" height="7" rx="1" fill="#0255a3"/>
        <circle cx="12" cy="14.5" r="1.8" fill="#ffffff"/>
      </svg>
      <svg viewBox="0 0 24 24" aria-label="Email">
        <rect width="24" height="24" fill="#ffffff"/>
        <rect x="5" y="7" width="14" height="10" fill="#0255a3"/>
        <path d="M5.5 7.5 12 13l6.5-5.5" fill="none" stroke="#ffffff" stroke-width="1.3"/>
      </svg>
      <svg viewBox="0 0 24 24" aria-label="Website">
        <rect width="24" height="24" fill="#ffffff"/>
        <circle cx="12" cy="12" r="7" fill="#0255a3"/>
        <path d="M9 8c2 1 1 3 3 3s1 3-1 4M14 6c0 2 2 2 3 3" fill="none" stroke="#ffffff" stroke-width="1.2"/>
      </svg>
      <span class="rule"></span>
    </div>
    <ul class="contact-list">
      <li>415 903 2276</li>
      <li>info@brightpawobedience.example</li>
      <li>www.brightpawobedience.example</li>
    </ul>
  </section>

  <section class="card card--back" aria-label="Card back">
    <p class="brand-name">Brightpaw Obedience</p>
    <div class="tagline-band">
      <p class="tagline">“Building calm, happy dogs one lesson at a time.”</p>
    </div>
  </section>
</main>
</body>
</html>
```